Machinery Harbor Corp - Business Card Design

Need a new modern designed business card that is different and stands out to represent my equipment financing company. Machinery Harbor Corp finances all types of equipment and all types of industries. We like to do equipment financing a different way by putting customers first and want our card to represent that different approach to business. I want a card that some remembers when they receive it so it sticks in their mind and makes that wow impression.

Card should have a black background so the logo stands out. It can be horizontial or vertical or a combination of both.

Front of card information is below that shows the information that would go on my card. That is where I want a different look or design to stand out. The front could be split black/orange colour so the logo could pop on black side and information on orange side with different lettering. Just outside the box thinking on the front of the card. Open to any type of design.

Back of card is below which i I like unless you have a different spin to provide or a different idea that would make the card better as I am open to anything that looks great.

Target Market(s)

Machinery Harbor Corp deals with business owners in all industries.

Industry/Entity Type

Business

Contact Information for Business Card

Colors

Designer to choose colors to be used in the design.

Requirements
Must have
• Modern
• Different
• Stand Out
• Makes an Impression

```html
<!DOCTYPE html>
<html lang="en">
<head>
<meta charset="utf-8">
<title>Machinery Harbor Corp – Business Card</title>
<link href="https://fonts.googleapis.com/css2?family=Lato:wght@400;700&display=swap" rel="stylesheet">
<style>
  :root {
    --backdrop: #4a4a4a;
    --card: #000000;
    --white: #ffffff;
    --orange: #f06a22;
    --steel: #8c8c8c;
  }
  html, body {
    margin: 0;
    padding: 0;
    overflow: hidden;
  }
  .canvas {
    position: relative;
    width: 1189px;
    height: 1200px;
    background: var(--backdrop);
    overflow: hidden;
    font-family: "Lato", Arial, sans-serif;
  }
  .card {
    position: absolute;
    left: 171px;
    width: 856px;
    height: 488px;
    background: var(--card);
    box-shadow: 0 6px 18px rgba(0,0,0,0.45);
  }
  .card--front {
    top: 67px;
    border-top-left-radius: 49px;
  }
  .card--back {
    top: 626px;
    border-top-right-radius: 49px;
  }
  .front-brand {
    position: absolute;
    left: 0;
    right: 0;
    top: 300px;
    text-align: center;
    color: var(--steel);
    font-size: 32px;
    font-weight: 400;
    letter-spacing: 4px;
    margin: 0;
  }
  .holder {
    position: absolute;
    left: 48px;
    top: 52px;
    margin: 0;
  }
  .holder__name {
    display: block;
    color: var(--white);
    font-size: 31px;
    font-weight: 700;
    line-height: 34px;
  }
  .holder__title {
    display: block;
    color: var(--orange);
    font-size: 23px;
    font-weight: 400;
    line-height: 30px;
    letter-spacing: 0.5px;
  }
  .contact-list {
    position: absolute;
    left: 48px;
    top: 226px;
    margin: 0;
    padding: 0;
    list-style: none;
  }
  .contact-list li {
    display: flex;
    align-items: center;
    height: 29px;
    color: var(--white);
    font-size: 21px;
  }
  .contact-list svg {
    width: 26px;
    height: 26px;
    margin-right: 14px;
    flex: none;
  }
  .back-brand {
    position: absolute;
    right: 48px;
    top: 392px;
    margin: 0;
    color: var(--orange);
    font-size: 28px;
    font-weight: 400;
    letter-spacing: 3px;
  }
</style>
</head>
<body>
<div class="canvas">
  <section class="card card--front">
    <p class="front-brand">MACHINERY HARBOR CORP</p>
  </section>

  <section class="card card--back">
    <p class="holder">
      <span class="holder__name">DEAN MARLOW</span>
      <span class="holder__title">PRESIDENT</span>
    </p>
    <ul class="contact-list">
      <li>
        <svg viewBox="0 0 26 26" aria-hidden="true">
          <circle cx="13" cy="13" r="11.5" fill="none" stroke="var(--orange)" stroke-width="1.6"/>
          <path d="M8 9.5h10v2h-2.5l-1-1.2h-3l-1 1.2H8z M8.5 12.5h9v5h-9z" fill="var(--orange)"/>
        </svg>
        555.010.4821
      </li>
      <li>
        <svg viewBox="0 0 26 26" aria-hidden="true">
          <circle cx="13" cy="13" r="11.5" fill="none" stroke="var(--orange)" stroke-width="1.6"/>
          <rect x="7.5" y="9" width="11" height="8" fill="var(--orange)"/>
          <path d="M7.5 9l5.5 4.5 5.5-4.5" fill="none" stroke="var(--card)" stroke-width="1"/>
        </svg>
        dean@machineryharborcorp.ca
      </li>
      <li>
        <svg viewBox="0 0 26 26" aria-hidden="true">
          <circle cx="13" cy="13" r="11.5" fill="none" stroke="var(--orange)" stroke-width="1.6"/>
          <circle cx="13" cy="13" r="6" fill="none" stroke="var(--orange)" stroke-width="1.3"/>
          <ellipse cx="13" cy="13" rx="2.6" ry="6" fill="none" stroke="var(--orange)" stroke-width="1"/>
          <path d="M7 13h12M8 10h10M8 16h10" stroke="var(--orange)" stroke-width="0.9"/>
        </svg>
        www.machineryharborcorp.ca
      </li>
    </ul>
    <p class="back-brand">MACHINERY HARBOR CORP</p>
  </section>
</div>
</body>
</html>
```